Brackenford Fluidworks needs a website describing the repair business we are in.

Brackenford Fluidworks is a full hydraulic repair facility. We have 2 shops. We repair and service all hydraulic cylinders, pneumatic cylinders, hydraulic pumps, motors, valves and gearboxes. Our services range from large industrial plants to the individual that owns one piece of equipment. We also offer removal and install of cylinders. Along with free pick up and delivery, within a certain distance which is usually 100 miles from one of our shops.

With over 30 years experience in the hydraulic business, we can repair or replace any job. There is not a job too big or too small, we service them all.

We have customers that send whole pieces of equipment to us to do complete overhauls on all the hydraulics. Ranging from a country club green roller to a 10 ton boom truck.

Target Market(s)

Industrial plants, road builders, dirt work companies, general contractors, owners of industrial equipment (bulldozers, excavators, loaders, scrapers, motor graders, etc.

Industry/Entity Type

Hydraulic

Number of Pages Required

5+ page

Font styles to use
Sans Serif

Colors
ec1f27
ffffff
aaaaaa

Requirements
Must have
• Information about what we offer and pictures of jobs completed.
Nice to have
• Nice stock photos of jobsites and industrial plants.
Should not have
• Any sort of comical characters.

```html
<!DOCTYPE html>
<html lang="en">
<head>
<meta charset="utf-8">
<title>Brackenford Fluidworks</title>
<link href="https://fonts.googleapis.com/css2?family=Roboto:ital,wght@0,400;0,500;0,700;1,400;1,700&display=swap" rel="stylesheet">
<style>
:root{
  --red:#ec1f27;
  --red-deep:#c8141c;
  --wine:#8c0f1c;
  --white:#ffffff;
  --grey:#aaaaaa;
  --ink:#1c1c1c;
  --body:#555555;
  --night:#1d2230;
  --foot:#9a9a9a;
}
*{margin:0;padding:0;box-sizing:border-box}
html,body{width:1200px;height:3327px;overflow:hidden}
body{font-family:'Roboto',Arial,sans-serif;color:var(--ink);background:var(--white);position:relative}
.abs{position:absolute}
section,header,footer,nav{position:absolute;left:0;width:1200px}

/* header */
.topbar{top:0;height:118px;background:var(--white)}
.brand{left:106px;top:18px;width:110px;text-align:center}
.brand-dot{width:46px;height:46px;border-radius:50%;background:var(--red);margin:0 auto 6px}
.brand-name{font-size:13px;font-weight:700;color:var(--red);line-height:1.1;text-transform:uppercase}
.info{top:40px;display:flex;gap:14px;align-items:center;font-size:12.5px;line-height:20px;color:var(--ink)}
.info b{font-weight:700}
.info svg{flex:none}

.mainnav{top:118px;height:40px;background:var(--red)}
.mainnav ul{list-style:none;display:flex;position:absolute;left:100px;top:0;height:40px}
.mainnav li{width:117px;text-align:center;line-height:40px;color:var(--white);font-size:13px;font-weight:500}
.mainnav li.active{background:var(--red-deep);width:95px}

/* hero */
.hero{top:158px;height:574px}
.hero-photo{position:absolute;inset:0;background:linear-gradient(180deg,#4a4d4f 0%,#6c6a64 35%,#5b564c 62%,#2d2b28 100%)}
.hero-shade{position:absolute;inset:0;background:rgba(0,0,0,.28)}
.hero h1{position:absolute;top:178px;width:100%;text-align:center;color:var(--white);font-size:56px;font-weight:700;letter-spacing:.5px}
.hero p{position:absolute;top:268px;width:100%;text-align:center;color:var(--white);font-size:25px}
.btn{display:inline-block;background:var(--red);color:var(--white);font-weight:500;border-radius:22px;text-align:center}
.hero .btn{position:absolute;left:524px;top:342px;width:150px;height:38px;line-height:38px;font-size:13px}
.dots{position:absolute;top:528px;left:560px;display:flex;gap:10px}
.dots i{width:11px;height:11px;border-radius:50%;background:var(--white)}
.dots i:first-child{background:transparent;border:2px solid var(--white)}

/* about */
.about{top:732px;height:555px}
.about h2{position:absolute;left:100px;top:82px;font-size:30px;font-weight:700;text-transform:uppercase}
.about .copy{position:absolute;left:100px;top:152px;width:525px;font-size:12.5px;line-height:24px;color:var(--body)}
.about .copy p+p{margin-top:14px}
.about .btn{position:absolute;left:100px;top:380px;width:140px;height:42px;line-height:42px;font-size:12px}
.frame{left:752px;top:113px;width:346px;height:324px;border:2px solid var(--red)}
.about-photo{left:672px;top:131px;width:408px;height:290px;background:linear-gradient(135deg,#3a3a3a,#8a7a5c 45%,#2f3a5a 70%,#2a2a2a)}

/* why */
.why{top:1287px;height:388px;background:linear-gradient(120deg,#0f1a2c,#2a3a52 45%,#5a3a2a 70%,#12202f)}
.why-box{left:100px;top:81px;width:215px;height:216px;border:2px solid var(--white);color:var(--white);font-size:30px;font-weight:700;text-align:center;display:flex;align-items:center;justify-content:center;line-height:38px}
.feature{top:82px;width:240px;text-align:center;color:var(--white)}
.feature .ico{width:92px;height:92px;border-radius:50%;background:var(--red);margin:0 auto;display:flex;align-items:center;justify-content:center}
.feature h3{margin-top:22px;font-size:16px;font-weight:500;text-transform:uppercase}
.feature p{margin-top:8px;font-size:11.5px;line-height:16px}
.feature .more{margin-top:6px;font-size:11.5px;font-weight:500}

/* blog */
.blog{top:1675px;height:676px}
.blog h2{position:absolute;top:84px;width:100%;text-align:center;font-size:30px;font-weight:700;text-transform:uppercase}
.post{top:179px;width:306px}
.post .thumb{height:200px;border:1px solid #ddd}
.post h3{margin-top:22px;font-size:15px;font-weight:700;line-height:24px;height:50px}
.post p{margin-top:8px;font-size:11.5px;line-height:20px;color:var(--body);height:62px}
.post .btn{margin-top:26px;width:130px;height:38px;line-height:38px;font-size:12px}

/* clients */
.clients{top:2351px;height:410px;background:var(--wine)}
.clients h2{position:absolute;top:56px;width:100%;text-align:center;color:var(--white);font-size:30px;font-weight:700;text-transform:uppercase}
.quote{top:125px;width:500px;text-align:center;color:var(--white)}
.quote p{font-size:11.5px;font-style:italic;font-weight:700;line-height:17px;height:80px}
.avatar{width:80px;height:80px;border-radius:50%;background:linear-gradient(180deg,#d8d4ce,#7a6a5c);border:3px solid var(--white);margin:0 auto}
.quote h4{margin-top:16px;font-size:15px;font-weight:700}
.quote small{display:block;margin-top:6px;font-size:11.5px;font-style:italic;font-weight:700}

/* contact */
.contact{top:2761px;height:493px;background:linear-gradient(180deg,#2a2e3c,#3a3f4e 60%,#23262f)}
.contact-card{left:118px;top:147px;width:302px;height:306px;border:2px solid var(--white);color:var(--white);padding:40px 24px}
.contact-card h2{font-size:30px;font-weight:500;text-transform:uppercase}
.contact-card p{margin-top:16px;font-size:12.5px;line-height:20px}
.contact-card ul{list-style:none;margin-top:18px;font-size:12.5px}
.contact-card li{display:flex;gap:18px;line-height:20px;margin-bottom:8px}
.contact-card li svg{flex:none;margin-top:4px}
.quote-form{left:501px;top:150px;width:579px;color:var(--white)}
.quote-form h2{font-size:30px;font-weight:500;text-transform:uppercase}
.quote-form .rule{width:140px;height:3px;background:var(--white);margin-top:12px}
.quote-form p{margin-top:28px;font-size:12.5px;line-height:22px;font-weight:500}
.fields{display:grid;grid-template-columns:280px 277px;gap:25px 22px;margin-top:32px}
.field{height:32px;background:var(--white);color:#444;font-size:12px;line-height:32px;padding-left:16px}
.submit{margin-top:28px;height:36px;background:var(--red);text-align:center;line-height:36px;font-size:12px;font-weight:700;text-transform:uppercase}

footer{top:3254px;height:73px;background:var(--foot);color:var(--white);font-size:12px;text-align:center;line-height:73px}
</style>
</head>
<body>

<header class="topbar">
  <div class="brand abs"><div class="brand-dot"></div><div class="brand-name">Brackenford Fluidworks</div></div>
  <div class="info abs" style="left:686px">
    <svg width="30" height="30" viewBox="0 0 30 30"><circle cx="15" cy="15" r="14" fill="#888"/><path d="M15 7v8l5 4" stroke="#fff" stroke-width="2.5" fill="none"/></svg>
    <div><b>Opening Hours:</b><br><b>Monday - Friday : 8.00 am-6.00 pm</b></div>
  </div>
  <div class="info abs" style="left:968px">
    <svg width="22" height="34" viewBox="0 0 22 34"><rect x="2" y="1" width="18" height="32" rx="3" fill="none" stroke="#888" stroke-width="2.5"/><circle cx="11" cy="28" r="1.6" fill="#888"/></svg>
    <div><b>Call Us Now :</b><br><b>1.555.014.2290</b></div>
  </div>
</header>

<nav class="mainnav">
  <ul><li class="active">Home</li><li>About us</li><li>Services</li><li>Projects</li><li>Blog</li><li>Shop</li><li>Contact us</li></ul>
</nav>

<section class="hero">
  <div class="hero-photo" role="img" aria-label="Photo of a repaired yellow hydraulic cylinder strapped on a flatbed trailer outside the shop"></div>
  <div class="hero-shade"></div>
  <h1>BRACKENFORD FLUIDWORKS</h1>
  <p>Ut enim ad minima veniam, quis nostrum exercitationem ullam</p>
  <span class="btn">LEARN MORE</span>
  <div class="dots"><i></i><i></i><i></i><i></i></div>
</section>

<section class="about">
  <h2>About Brackenford Fluidworks</h2>
  <div class="copy">
    <p>Brackenford Fluidworks is a full hydraulic repair facility. We have 2 shops. We repair and service all hydraulic cylinders, pneumatic cylinders, hydraulic pumps, motors, valves and gear boxes. Our services range from large industrial plants to the individual that owns one piece of equipment. We also offer removal and install of cylinders. Along with free pick up &amp; delivery, within a certain distance which is usually 100 miles from one of our shops.</p>
    <p>With over 30 years experience in the hydraulic business, we can repair or replace any job. There is not a job too big or too small, we service them all.</p>
  </div>
  <span class="btn">READ MORE &gt;&gt;</span>
  <div class="frame abs"></div>
  <div class="about-photo abs" role="img" aria-label="Photo of a rebuilt blue hydraulic pump on a wooden pallet"></div>
</section>

<section class="why" role="img" aria-label="Background photo of an industrial plant's pipework">
  <div class="why-box abs">WHY<br>CHOOSE<br>US</div>
  <div class="feature abs" style="left:350px">
    <div class="ico"><svg width="44" height="44" viewBox="0 0 44 44" fill="#fff"><path d="M10 18a12 12 0 0124 0z"/><rect x="8" y="18" width="28" height="3"/><circle cx="22" cy="26" r="6"/><path d="M8 44c0-8 6-12 14-12s14 4 14 12z"/></svg></div>
    <h3>Expert Engineers</h3>
    <p>Sed quia non numquam eius modi tempo ra incidunt ut labore et dolore magnam aliq quam quaera.</p>
    <div class="more">READ MORE &gt;&gt;</div>
  </div>
  <div class="feature abs" style="left:610px">
    <div class="ico"><svg width="44" height="44" viewBox="0 0 44 44" fill="#fff"><circle cx="22" cy="14" r="9"/><path d="M6 44c0-10 7-16 16-16s16 6 16 16z"/></svg></div>
    <h3>30 Years Experience</h3>
    <p>Sed quia non numquam eius modi tempo ra incidunt ut labore et dolore magnam aliq quam quaera.</p>
    <div class="more">READ MORE &gt;&gt;</div>
  </div>
  <div class="feature abs" style="left:871px">
    <div class="ico"><svg width="50" height="36" viewBox="0 0 50 36" fill="#fff"><rect x="2" y="4" width="30" height="22"/><path d="M34 10h8l6 8v8H34z"/><circle cx="12" cy="29" r="5"/><circle cx="40" cy="29" r="5"/></svg></div>
    <h3>Delivery On Time</h3>
    <p>Sed quia non numquam eius modi tempo ra incidunt ut labore et dolore magnam aliq quam quaera.</p>
    <div class="more">READ MORE &gt;&gt;</div>
  </div>
</section>

<section class="blog">
  <h2>Blog Post</h2>
  <article class="post abs" style="left:100px">
    <div class="thumb" role="img" aria-label="Photo of a yellow hydraulic cylinder close up" style="background:linear-gradient(135deg,#3a2f22,#e3c02a 50%,#4a3a28)"></div>
    <h3>Lorem Ipsum is that it has a more-or-less normal distribution</h3>
    <p>Sed ut perspiciatis unde omnis iste natus error voluptatem accusantium doloremque laudantium, totam rem aperiam, eaque ipsa quae ab illo inventore veritatis et.</p>
    <span class="btn">READ MORE &gt;&gt;</span>
  </article>
  <article class="post abs" style="left:446px">
    <div class="thumb" role="img" aria-label="Photo of rebuilt cylinder rods laid on a pallet" style="background:linear-gradient(180deg,#b8b2a6,#8e8a82 50%,#a08660)"></div>
    <h3>Contrary to popular belief, Lorem Ipsum is not simply random</h3>
    <p>Quis autem vel eum iure reprehenderit qui in ea voluptate velit esse quam nihil molestiae consequatur, vel illum qui dolorem eum fugiat quo voluptas nulla pariatur.</p>
    <span class="btn">READ MORE &gt;&gt;</span>
  </article>
  <article class="post abs" style="left:792px">
    <div class="thumb" role="img" aria-label="Photo of an orange hydraulic cylinder in a truck bed" style="background:linear-gradient(180deg,#3a3f48,#d9521e 55%,#2a2a2a)"></div>
    <h3>The standard chunk of Lorem Ipsum used since the 1500s</h3>
    <p>Nor again is there anyone who loves or pursues desires to obtain itself, because it is pain, but because occasionally circumstances occur in which toil and pain can procure.</p>
    <span class="btn">READ MORE &gt;&gt;</span>
  </article>
</section>

<section class="clients">
  <h2>Our Clients</h2>
  <div class="quote abs" style="left:110px">
    <p>" Sed ut perspiciatis unde omnis iste natus error sit voluptatem accusantium doloremque laudantium, totam rem aperiam, eaque ipsa quae ab illo inventore veritatis et quasi architecto beatae vitae dicta sunt explicabo. Nemo enim ipsam voluptatem quia "</p>
    <div class="avatar" role="img" aria-label="Client portrait"></div>
    <h4>- Author Name</h4><small>- City Location</small>
  </div>
  <div class="quote abs" style="left:635px">
    <p>" Sed ut perspiciatis unde omnis iste natus error sit voluptatem accusantium doloremque laudantium, totam rem aperiam, eaque ipsa quae ab illo inventore veritatis et quasi architecto beatae vitae dicta sunt explicabo. Nemo enim ipsam voluptatem quia "</p>
    <div class="avatar" role="img" aria-label="Client portrait"></div>
    <h4>- Author Name</h4><small>- City Location</small>
  </div>
</section>

<section class="contact" role="img" aria-label="Background photo of a refinery at dusk">
  <svg class="abs" style="left:0;top:-40px" width="1200" height="110" viewBox="0 0 1200 110"><path d="M0 110 L0 75 Q600 -10 1200 75 L1200 110 Z" fill="#2a2e3c"/></svg>
  <div class="contact-card abs">
    <h2>Contact</h2>
    <p>For any kind of query, contact us<br>with the details below.</p>
    <ul>
      <li><svg width="12" height="12" viewBox="0 0 12 12" fill="#fff"><path d="M2 0l3 3-1.5 2a8 8 0 003.5 3.5L9 7l3 3-2 2C5 12 0 7 0 2z"/></svg>1.555.014.2290</li>
      <li><svg width="12" height="10" viewBox="0 0 12 10" fill="#fff"><rect width="12" height="10"/><path d="M0 0l6 5 6-5" stroke="#2a2e3c" fill="none"/></svg>info@brackenfordfluidworks.com</li>
      <li><svg width="12" height="14" viewBox="0 0 12 14" fill="#fff"><path d="M6 0a6 6 0 016 6c0 4-6 8-6 8S0 10 0 6a6 6 0 016-6z"/><circle cx="6" cy="6" r="2" fill="#2a2e3c"/></svg>#412, Alder Row, Fenwick Bay<br>Northshire</li>
    </ul>
  </div>
  <div class="quote-form abs">
    <h2>Request a Quote</h2>
    <div class="rule"></div>
    <p>Lorem ipsum dolor sit amet, consectetur adipi scing elit, sed do eiusmod tempor<br>incidi dunt ut laboreet dolore magna aliqua.</p>
    <div class="fields">
      <div class="field">Name</div><div class="field">Email</div>
      <div class="field">Phone Number</div><div class="field">Your Enquiry</div>
    </div>
    <div class="submit">Submit</div>
  </div>
</section>

<footer>Copyright © 2018 Brackenford Fluidworks . All rights reserved.</footer>

</body>
</html>
```